I need a SEO-friendly Wordpress website (making sure to style H1, H2, H3, etc correctly) for a Hawaii-based law firm called Meridian Crest Legal Group. Comparable websites include https://brvlaw.example/ and https://www.lomrit.example/ for design reference. The current copy on the TarnAdvocate.example website can be used.

```html
<!DOCTYPE html>
<html lang="en">
<head>
<meta charset="utf-8">
<title>Meridian Crest Legal Group – Divorce and Personal Injury Lawyers</title>
<link rel="stylesheet" href="https://fonts.googleapis.com/css2?family=Open+Sans:wght@400;600;700&family=Noto+Serif:ital,wght@0,400;0,700;1,400&display=swap">
<style>
:root{
  --amber:#b5610f;
  --rust:#8a3309;
  --rust-dark:#7a2c07;
  --ink:#222222;
  --body:#555555;
  --line:#e6e6e6;
  --footer:#262626;
  --footer-deep:#202020;
  --field:#3a3a3a;
  --white:#ffffff;
  --map-land:#ececea;
  --map-water:#aac7ee;
}
*{box-sizing:border-box;margin:0;padding:0}
html,body{width:1200px;height:2594px;overflow:hidden}
body{font-family:"Open Sans",Arial,sans-serif;color:var(--body);background:var(--white);position:relative}
a{color:inherit;text-decoration:none}
svg{display:block}

/* top bar */
.topbar{position:absolute;top:0;left:0;width:1200px;height:36px;background:linear-gradient(90deg,var(--amber) 0%,var(--amber) 60%,var(--rust-dark) 100%);color:var(--white);font-size:9px}
.topbar .item{position:absolute;top:12px;display:flex;align-items:center;gap:5px}
.topbar .email{left:233px}
.topbar .addr{left:570px}
.topbar .dir{left:883px;font-size:10.5px;font-weight:700;top:11px}

/* header */
.header{position:absolute;top:36px;left:0;width:1200px;height:82px;border-bottom:1px solid var(--line)}
.brand{position:absolute;left:233px;top:28px}
.brand-name{font-size:15px;font-weight:700;color:var(--rust);letter-spacing:.1px}
.brand-tag{font-family:"Noto Serif",Georgia,serif;font-style:italic;font-size:11px;color:#c98a4f;margin-top:2px;letter-spacing:.4px}
.call{position:absolute;left:756px;top:20px;display:flex;gap:12px;align-items:center}
.call-label{font-family:"Noto Serif",Georgia,serif;font-style:italic;font-size:11.5px;color:var(--ink)}
.call-num{font-size:19px;font-weight:700;color:var(--amber);margin-top:1px;margin-left:4px}

/* nav */
.nav{position:absolute;top:118px;left:0;width:1200px;height:42px;border-bottom:1px solid var(--line)}
.nav ul{list-style:none;position:absolute;left:233px;top:15px;display:flex;gap:27px;font-size:9.5px;font-weight:600;color:var(--ink)}
.nav .active{color:var(--amber)}
.nav .cta{position:absolute;left:804px;top:0;width:161px;height:42px;background:var(--rust);color:var(--white);font-size:11px;font-weight:600;display:flex;align-items:center;justify-content:center;letter-spacing:.3px}

/* hero */
.hero{position:absolute;top:160px;left:0;width:1200px;height:375px;background:linear-gradient(100deg,#6b5a4c 0%,#3d3f47 30%,#4a4d57 55%,#6b4a2f 65%,#9aa0a8 85%,#d9dbde 100%)}
.hero-card{position:absolute;left:403px;top:95px;width:393px;height:188px;background:rgba(181,97,15,.92);color:var(--white);text-align:center}
.hero-card .frame{position:absolute;inset:9px;border:1px solid rgba(255,255,255,.8);padding-top:20px}
.hero-card p{font-size:11px;font-weight:600;line-height:1.35}
.hero-card h1{font-size:15px;font-weight:700;line-height:1.35;margin:4px 0 14px}
.hero-card .intro{margin-bottom:18px}

/* about */
.about-head{position:absolute;left:233px;top:597px;border-left:2px solid var(--amber);padding-left:14px;height:42px}
.eyebrow{font-size:10.5px;font-weight:700;color:var(--amber);letter-spacing:.2px}
.about-head h2{font-size:20px;font-weight:600;color:var(--ink);margin-top:4px;letter-spacing:.2px}
.about-sub{position:absolute;left:234px;top:666px;font-size:13.5px;font-weight:700;color:var(--amber)}
.about-copy{position:absolute;left:234px;top:702px;width:419px;font-size:8.6px;line-height:15px;text-align:justify;color:#444}
.about-copy p+p{margin-top:15px}
.btn-more{position:absolute;left:234px;top:855px;width:128px;height:28px;background:var(--rust);color:var(--white);font-size:8.5px;font-weight:700;display:flex;align-items:center;justify-content:center}
.enquiry{position:absolute;left:390px;top:852px}
.enquiry .q{font-size:9px;font-weight:700;color:var(--ink)}
.enquiry .n{font-size:14px;font-weight:700;color:var(--amber);margin-top:4px}
.about-photo{position:absolute;left:671px;top:597px;width:294px;height:290px;background:linear-gradient(160deg,#6f6a66 0%,#a8a29b 45%,#d8d2c6 70%,#8f6a3e 100%)}
.about-photo .frame{position:absolute;left:12px;top:12px;right:12px;bottom:12px;border:1px solid rgba(255,255,255,.85)}

/* consultation band */
.band{position:absolute;left:0;width:1200px;height:156px;overflow:hidden}
.band-1{top:942px;background:var(--amber)}
.band-2{top:1947px;background:var(--rust)}
.band .chev{position:absolute;left:0;top:0}
.band .lead{position:absolute;left:233px;top:50px;font-family:"Noto Serif",Georgia,serif;color:var(--white)}
.band .lead small{display:block;font-size:17px}
.band .lead strong{display:block;font-size:32px;font-weight:700;letter-spacing:.3px;line-height:1.15}
.band .ring{position:absolute;left:666px;top:55px;width:47px;height:47px;border-radius:50%;display:flex;align-items:center;justify-content:center}
.band-1 .ring{background:var(--rust)}
.band-2 .ring{background:var(--amber)}
.band .num{position:absolute;left:726px;top:57px;font-family:"Noto Serif",Georgia,serif;font-size:31px;color:var(--white)}

/* practice areas */
.section-title{position:absolute;left:0;width:1200px;top:1154px;text-align:center}
.section-title .eyebrow{display:inline-flex;align-items:center;gap:14px}
.section-title .eyebrow::before,.section-title .eyebrow::after{content:"";width:36px;height:1px;background:var(--amber)}
.section-title h2{font-size:20px;font-weight:600;color:var(--ink);margin-top:5px}
.areas{position:absolute;left:233px;top:1233px;display:flex;gap:19px}
.area{width:169px}
.area .shot{height:143px}
.area h3{font-size:11.5px;font-weight:700;color:var(--ink);margin-top:16px;line-height:15px;letter-spacing:.1px}
.area p{font-size:8.6px;line-height:15px;margin-top:6px;color:#444}
.shot-family{background:linear-gradient(135deg,#c9a27a,#e9dccb 50%,#8fa6c2)}
.shot-injury{background:linear-gradient(135deg,#d7d7d7,#3a3a3a 50%,#9a9a9a)}
.shot-corporate{background:linear-gradient(170deg,#f2f4f6,#8aa3bb 55%,#4d6a87)}
.shot-estate{background:linear-gradient(180deg,#7fa3cf 0%,#b9cde3 30%,#4c7a3a 55%,#6ba24a 100%)}

/* location map area */
.map{position:absolute;top:1542px;left:0;width:1200px;height:405px;background:linear-gradient(90deg,var(--map-water) 0%,var(--map-water) 16%,var(--map-land) 28%,var(--map-land) 100%)}

/* footer */
.footer{position:absolute;top:2103px;left:0;width:1200px;height:405px;background:var(--footer)}
.f-brand{position:absolute;left:233px;top:77px}
.f-brand .brand-name{color:var(--white)}
.f-brand .brand-tag{color:var(--amber)}
.f-links{position:absolute;left:250px;top:123px;display:grid;grid-template-columns:110px 110px;column-gap:22px;list-style:none;font-size:11px;color:#d8d8d8}
.f-links li{height:30px;display:flex;align-items:center;gap:9px;border-bottom:1px solid #333}
.f-links li::before{content:"";border-left:4px solid var(--amber);border-top:3px solid transparent;border-bottom:3px solid transparent}
.f-links li:nth-last-child(-n+2){border-bottom:none}
.f-head{position:absolute;font-size:14px;font-weight:700;color:var(--white);display:flex;align-items:center;gap:10px}
.f-head::after{content:"";height:1px;background:#3c3c3c;flex:1}
.follow{left:233px;top:242px;width:294px}
.reach{left:547px;top:74px;width:418px}
.socials{position:absolute;left:236px;top:284px;display:flex;gap:8px}
.socials span{width:38px;height:38px;border-radius:50%;background:#333}
.field{position:absolute;background:var(--field);color:#9a9a9a;font-size:8px;padding:11px 10px}
.send{position:absolute;left:547px;top:299px;width:418px;height:34px;background:var(--amber);color:var(--white);font-size:11px;font-weight:700;display:flex;align-items:center;justify-content:space-between;padding:0 14px 0 18px;letter-spacing:.3px}
.copyright{position:absolute;top:2508px;left:0;width:1200px;height:86px;background:var(--footer-deep);border-top:1px solid #2f2f2f;text-align:center;font-size:8.6px;color:#9a9a9a;padding-top:39px}
</style>
</head>
<body>

<div class="topbar">
  <div class="item email">
    <svg width="10" height="8" viewBox="0 0 10 8"><rect x=".5" y=".5" width="9" height="7" fill="none" stroke="#fff"/><path d="M.5 .5 5 4.5 9.5 .5" fill="none" stroke="#fff"/></svg>
    clients@tarnadvocate.example
  </div>
  <div class="item addr">
    <svg width="8" height="10" viewBox="0 0 8 10"><path d="M4 9.5C1.5 6 .5 4.8.5 3.5a3.5 3.5 0 0 1 7 0C7.5 4.8 6.5 6 4 9.5z" fill="none" stroke="#fff"/><circle cx="4" cy="3.5" r="1.2" fill="#fff"/></svg>
    74-210 Palani Court, Suite 210, Kailua Kona, Hawaii 96740.
  </div>
  <a class="item dir" href="#">Get Direction
    <svg width="12" height="7" viewBox="0 0 12 7"><path d="M0 3.5h10.5M8 .8l2.8 2.7L8 6.2" fill="none" stroke="#fff" stroke-width="1.3"/></svg>
  </a>
</div>

<header class="header">
  <div class="brand">
    <div class="brand-name">MERIDIAN CREST LEGAL GROUP</div>
    <div class="brand-tag">Divorce and Personal Injury Lawyers</div>
  </div>
  <div class="call">
    <svg width="32" height="32" viewBox="0 0 32 32"><circle cx="16" cy="16" r="15" fill="none" stroke="#b5610f" stroke-width="1.6"/><path d="M11.5 9.5l2.6-.4 1.4 3.4-1.7 1.3a9 9 0 0 0 4 4l1.3-1.7 3.4 1.4-.4 2.6c-.2.8-1 1.2-1.8 1.1-5.6-.8-9.4-4.6-10.2-10.2-.1-.8.4-1.4 1.4-1.5z" fill="none" stroke="#b5610f" stroke-width="1.4" stroke-linejoin="round"/></svg>
    <div>
      <div class="call-label">Call For Your Free Appointment</div>
      <div class="call-num">+1.808.555.0147</div>
    </div>
  </div>
</header>

<nav class="nav">
  <ul>
    <li class="active">HOME</li>
    <li>ABOUT US</li>
    <li>PRACTICE AREAS</li>
    <li>ATTORNEYS</li>
    <li>BLOG</li>
    <li>CONTACT US</li>
  </ul>
  <a class="cta" href="#">FREE CONSULTATION</a>
</nav>

<section class="hero" role="img" aria-label="Photo of a lawyer holding an open law book beside a wooden judge's gavel">
  <div class="hero-card">
    <div class="frame">
      <p class="intro">Kona Lawyers of MCLG -Legal kōkua with aloha.</p>
      <p>Over 70 years of combined practice, specializing in:</p>
      <h1>Personal Injury, Family &amp; Divorce<br>Child Custody</h1>
      <p>Dedicated to making sure you receive the care and<br>attention you need.</p>
    </div>
  </div>
</section>

<section class="about">
  <div class="about-head">
    <div class="eyebrow">WHO WE ARE</div>
    <h2>ABOUT THE KONA LAWYERS OF MCLG</h2>
  </div>
  <h3 class="about-sub">Lawyers Serving the Big Island and Neighboring Islands</h3>
  <div class="about-copy">
    <p>The experienced attorneys in the Meridian Crest Legal Group's Kailua Kona, Hawaii office provide clients with a wide range of litigation expertise, including legal claims involving divorce &amp; family, personal injury, toxic exposures, intellectual property, and real estate.</p>
    <p>Our Kona office also offers commercial and hospitality litigation expertise on behalf of a wide variety of clients, including restaurants, hotels, property owners, and many others. We never wish to see our clients go to court, though if there is no other option, you're in safe hands with our seasoned trial lawyers and the many years of courtroom experience behind them.</p>
  </div>
  <a class="btn-more" href="#">More About Us</a>
  <div class="enquiry">
    <div class="q">For Any Enquiry and Question Please Call us 24/7</div>
    <div class="n">+1.808.555.0147</div>
  </div>
  <div class="about-photo" role="img" aria-label="Photo of an attorney reading at a desk behind brass scales of justice"><div class="frame"></div></div>
</section>

<section class="band band-1">
  <svg class="chev" width="1200" height="156"><polygon points="0,0 590,0 636,78 590,156 0,156" fill="#b86512"/></svg>
  <div class="lead"><small>Call us now No Recovery, No Fee</small><strong>FREE CONSULTATION</strong></div>
  <div class="ring"><svg width="22" height="22" viewBox="0 0 22 22"><path d="M5 3l3-.4 1.6 3.8-1.9 1.4a10 10 0 0 0 4.5 4.5l1.4-1.9 3.8 1.6-.4 3c-.2.9-1.1 1.3-2 1.2C8.6 15.3 4.7 11.4 3.8 5.2 3.7 4.3 4.1 3.2 5 3z" fill="none" stroke="#fff" stroke-width="1.2"/><path d="M13 2.5a7 7 0 0 1 6.5 6.5M13 5.5a4 4 0 0 1 3.5 3.5" fill="none" stroke="#fff" stroke-width="1.2"/></svg></div>
  <div class="num">+1.808.555.0147</div>
</section>

<section class="practice">
  <div class="section-title">
    <div class="eyebrow">WHAT WE DO</div>
    <h2>OUR PRACTICE AREAS</h2>
  </div>
  <div class="areas">
    <article class="area">
      <div class="shot shot-family" role="img" aria-label="Photo of a smiling older couple reading documents together at home"></div>
      <h3>FAMILY &amp; DIVORCE</h3>
      <p>Our lawyers handle all aspects of family law on the Big Island and neighboring islands. We have more than 70 years of combined experience handling divorce</p>
    </article>
    <article class="area">
      <div class="shot shot-injury" role="img" aria-label="Black and white photo of a person with an arm injury"></div>
      <h3>PERSONAL INJURY</h3>
      <p>Dealing with personal injury and wrongful death claims is hard enough, so the lawyers of MCLG are here to make things as easy on you as possible.</p>
    </article>
    <article class="area">
      <div class="shot shot-corporate" role="img" aria-label="Photo of a glass office tower against the sky"></div>
      <h3>CORPORATE &amp; INTELLECTUAL PROPERTY</h3>
      <p>The attorneys at MCLG have been helping Big Island business owners with all their legal needs, so they can stay focused on what matters.</p>
    </article>
    <article class="area">
      <div class="shot shot-estate" role="img" aria-label="Photo of a large house behind a green lawn and trees"></div>
      <h3>REAL ESTATE</h3>
      <p>Our lawyers work with home owners, buyers and property developers to ensure timely handling of all legal aspects involved in real estate.</p>
    </article>
  </div>
</section>

<section class="map" role="img" aria-label="Street map of Kailua Kona with the bay on the left, marking the office location with its address and contact details"></section>

<section class="band band-2">
  <svg class="chev" width="1200" height="156"><polygon points="0,0 590,0 636,78 590,156 0,156" fill="#8e360a"/></svg>
  <div class="lead"><small>Call us now No Recovery, No Fee</small><strong>FREE CONSULTATION</strong></div>
  <div class="ring"><svg width="22" height="22" viewBox="0 0 22 22"><path d="M5 3l3-.4 1.6 3.8-1.9 1.4a10 10 0 0 0 4.5 4.5l1.4-1.9 3.8 1.6-.4 3c-.2.9-1.1 1.3-2 1.2C8.6 15.3 4.7 11.4 3.8 5.2 3.7 4.3 4.1 3.2 5 3z" fill="none" stroke="#fff" stroke-width="1.2"/><path d="M13 2.5a7 7 0 0 1 6.5 6.5M13 5.5a4 4 0 0 1 3.5 3.5" fill="none" stroke="#fff" stroke-width="1.2"/></svg></div>
  <div class="num">+1.808.555.0147</div>
</section>

<footer class="footer">
  <div class="f-brand">
    <div class="brand-name">MERIDIAN CREST LEGAL GROUP</div>
    <div class="brand-tag">Divorce and Personal Injury Lawyers</div>
  </div>
  <ul class="f-links">
    <li>Home</li><li>Attorneys</li>
    <li>About us</li><li>Blog</li>
    <li>Practice Areas</li><li>Contact Us</li>
  </ul>
  <div class="f-head follow">FOLLOW US</div>
  <div class="socials" aria-label="Social profiles"><span></span><span></span><span></span><span></span></div>

  <div class="f-head reach">REACH OUT TO US</div>
  <div class="field" style="left:547px;top:112px;width:203px;height:30px">First Name</div>
  <div class="field" style="left:762px;top:112px;width:203px;height:30px">Last Name</div>
  <div class="field" style="left:547px;top:155px;width:203px;height:30px">Email</div>
  <div class="field" style="left:762px;top:155px;width:203px;height:30px">Subject</div>
  <div class="field" style="left:547px;top:199px;width:418px;height:78px">Message</div>
  <a class="send" href="#">SEND MESSAGE
    <svg width="17" height="13" viewBox="0 0 17 13"><rect width="17" height="13" rx="1.5" fill="#fff"/><path d="M1 1.5l7.5 6 7.5-6" fill="none" stroke="#b5610f" stroke-width="1.4"/></svg>
  </a>
</footer>

<div class="copyright">Copyright © 2019 Meridian Crest Legal Group. All Rights Reserved</div>

</body>
</html>
```